Automotive component supplier needs a business card design

We need a business card design for our company called Velran Global Components Ltd based in the UK. We are a supplier of interior and exterior components to premium car manufacturers such as Corvel Ashby, Hadley Fenn, Marquist and Tavarelli. We would like to see a modern business card design that uses the colour blue.

Target Market(s)

Premium automotive car manufacturers.

Industry/Entity Type

Automotive

Contact Information for Business Card

Company Name : Velran Global Components Limited
Address: 17 Marlow Yard, Upper Heath, Warwick, CV31 8QL, United Kingdom
Web Address : www.velrancomponents-example.co.uk

Font styles to use
Other font styles liked:
• Helvetica

Colors
3176b5
0255a3
85acd3
cfdeed
cee9f5
85cae6
34a6d7
0692cd
9bcb3c

Requirements
Must have
• Clear company logo and a mixture of blue colours.
Nice to have
• A high quality modern image.
Should not have
• Multiple colours.

```html
<!DOCTYPE html>
<html lang="en">
<head>
<meta charset="utf-8">
<title>Velran Global Components – Business Card</title>
<link rel="stylesheet" href="https://fonts.googleapis.com/css2?family=Saira:wght@400;600;700&display=swap">
<style>
  :root {
    --blue: #0692cd;
    --blue-deep: #0a8fcf;
    --green: #9bcb3c;
    --ink: #4a4a4a;
    --paper: #ffffff;
    --backdrop: #2a2a2a;
  }
  * { box-sizing: border-box; margin: 0; padding: 0; }
  html, body {
    width: 1200px; height: 987px; overflow: hidden;
    background: var(--backdrop);
    font-family: "Saira", "Helvetica Neue", Arial, sans-serif;
  }
  .stage { position: relative; width: 1200px; height: 987px; }

  .card {
    position: absolute; left: 293px; width: 615px; height: 352px;
    box-shadow: 0 6px 18px rgba(0,0,0,0.45);
  }
  .card--front { top: 130px; background: var(--paper); }
  .card--back { top: 505px; background: var(--blue-deep); }

  .accent-bar {
    position: absolute; left: 0; top: 50px; width: 15px; height: 51px;
    background: var(--blue);
  }
  .holder { position: absolute; left: 39px; top: 50px; }
  .holder__name {
    font-weight: 700; font-size: 22px; color: var(--blue);
    letter-spacing: 0.5px; line-height: 1.2;
  }
  .holder__role { font-size: 15px; color: var(--green); line-height: 1.3; }

  .wordmark {
    position: absolute; font-weight: 700; text-transform: uppercase;
    display: flex; align-items: flex-start; gap: 8px;
  }
  .wordmark__dot { width: 12px; height: 12px; background: var(--green); margin-top: 10px; flex: none; }
  .wordmark__name { display: block; line-height: 0.95; letter-spacing: 2px; }
  .wordmark__sub { display: block; letter-spacing: 1.4px; line-height: 1.2; }

  .wordmark--front { right: 40px; top: 40px; color: var(--blue); }
  .wordmark--front .wordmark__name { font-size: 54px; }
  .wordmark--front .wordmark__sub { font-size: 14px; }

  .wordmark--back {
    left: 0; right: 0; top: 118px; justify-content: center; color: var(--paper);
  }
  .wordmark--back .wordmark__dot { background: var(--paper); width: 16px; height: 16px; margin-top: 14px; }
  .wordmark--back .wordmark__name { font-size: 76px; letter-spacing: 3px; }
  .wordmark--back .wordmark__sub { font-size: 19px; letter-spacing: 2px; }

  .contacts {
    position: absolute; left: 39px; top: 250px; list-style: none;
    font-size: 16px; color: var(--ink);
  }
  .contacts li { display: flex; align-items: center; gap: 8px; height: 23.5px; }
  .contacts svg { width: 15px; height: 15px; fill: var(--blue); flex: none; }
  .contacts .email { font-size: 15px; }

  .address {
    position: absolute; right: 40px; top: 253px; text-align: right;
    font-style: normal; font-size: 16px; line-height: 22.5px; color: var(--ink);
  }
</style>
</head>
<body>
<main class="stage">
  <section class="card card--front" aria-label="Business card front">
    <div class="accent-bar"></div>
    <div class="holder">
      <p class="holder__name">MARA ELLISON</p>
      <p class="holder__role">CEO/Founder</p>
    </div>
    <div class="wordmark wordmark--front">
      <span class="wordmark__dot"></span>
      <span>
        <span class="wordmark__name">Velran</span>
        <span class="wordmark__sub">Global Components</span>
      </span>
    </div>
    <ul class="contacts">
      <li>
        <svg viewBox="0 0 16 16" aria-hidden="true"><path d="M3.6 1.2l2.3 2.6-1.2 2a9 9 0 0 0 5.5 5.5l2-1.2 2.6 2.3-1.2 2.2C8.1 15.6.4 7.9 1.4 2.4z"/></svg>
        <span>614 208 3791</span>
      </li>
      <li>
        <svg viewBox="0 0 16 16" aria-hidden="true"><path d="M4.5 0h7A1.5 1.5 0 0 1 13 1.5v13a1.5 1.5 0 0 1-1.5 1.5h-7A1.5 1.5 0 0 1 3 14.5v-13A1.5 1.5 0 0 1 4.5 0zM5 2v10h6V2zm3 11a1 1 0 1 0 0 2 1 1 0 0 0 0-2z"/></svg>
        <span>742 519 6083</span>
      </li>
      <li class="email">
        <svg viewBox="0 0 16 16" aria-hidden="true"><path d="M1 3h14v10H1zm1.5 1.2V5l5.5 4 5.5-4v-.8z"/></svg>
        <span>mara@velrancomponents-example.co.uk</span>
      </li>
    </ul>
    <address class="address">
      17 Marlow Yard, Upper Heath<br>
      Warwick, CV31 8QL<br>
      United Kingdom
    </address>
  </section>

  <section class="card card--back" aria-label="Business card back">
    <div class="wordmark wordmark--back">
      <span class="wordmark__dot"></span>
      <span>
        <span class="wordmark__name">Velran</span>
        <span class="wordmark__sub">Global Components</span>
      </span>
    </div>
  </section>
</main>
</body>
</html>
```